Corporate web site design for a blockchain oriented company

Design a web site for Velmora. The company works on blockchain projects, mostly in B2B . Logo and content of the web site are attached with the project.

Corporate web sites means that we need to present the company and, at least, two of its projects.

Target Market(s)

B2B (Telecom, Gvt, online e-commerce web sites, banks, insurance ...)

Number of Pages Required

3 page

Font styles to use
Sans Serif

Requirements
Must have
• Landing page
• Page for KYC product
• Page for Loyalty product
• Team presentation
• Contact form
• Company presentation
• Several section can be in one page.
Nice to have
• Teaser video per project.
Should not have
• Heavy web site with a lot of animations.

```html
<!DOCTYPE html>
<html lang="en">
<head>
<meta charset="utf-8">
<title>Velmora — Blockchain Technology</title>
<link href="https://fonts.googleapis.com/css2?family=Rajdhani:wght@600;700&family=Lato:wght@400;700&family=Open+Sans:ital@1&display=swap" rel="stylesheet">
<style>
:root{
  --ink:#111111;
  --hero:#1c1c1c;
  --deep:#050505;
  --dark-band:#1f1f1f;
  --orange:#f7a400;
  --white:#ffffff;
  --muted:#5a5a5a;
  --soft:#f3f3f3;
  --grey:#8a8a8a;
  --link:#3a7ca5;
}
*{box-sizing:border-box;margin:0;padding:0}
html,body{width:1200px;height:3340px;overflow:hidden;background:var(--white)}
body{position:relative;font-family:"Lato",Arial,sans-serif;color:var(--ink)}
.abs{position:absolute}
.display{font-family:"Rajdhani","Arial Narrow",sans-serif;font-weight:700;text-transform:uppercase}
.btn{position:absolute;display:flex;align-items:center;justify-content:center;gap:10px;border-radius:24px;font-weight:700;font-size:15px;letter-spacing:.5px;text-transform:uppercase}
.btn svg{width:22px;height:12px}
.btn-orange{background:var(--orange);color:var(--white)}
.btn-dark{background:var(--ink);color:var(--white)}

/* header + hero */
.hero{position:absolute;left:0;top:0;width:1200px;height:700px}
.brand{left:160px;top:36px;font-family:"Rajdhani",sans-serif;font-weight:700;font-size:40px;letter-spacing:6px;color:var(--white);display:flex;align-items:center;gap:14px}
.brand i{display:block;width:16px;height:16px;border-radius:50%;background:var(--white)}
.nav{left:462px;top:48px;display:flex;gap:22px;font-size:18px;color:var(--white)}
.hero-title{left:160px;top:205px;font-size:52px;line-height:52px;color:var(--white)}
.hero-sub{left:168px;top:313px;width:380px;font-size:20px;line-height:26px;color:var(--white)}
.hero-art{left:630px;top:95px;width:440px;height:510px}
.dots{left:552px;top:600px;display:flex;gap:6px;align-items:center}
.dots span{width:8px;height:8px;border-radius:50%;background:#777}
.dots .on{background:var(--white)}
.dots .arrow{width:16px;height:16px;background:var(--white)}

/* why */
.why-mark{left:170px;top:800px;width:340px;height:160px;display:flex;align-items:center;justify-content:center;font-family:"Rajdhani",sans-serif;font-weight:700;font-size:66px;letter-spacing:6px;color:var(--ink)}
.why-title{left:548px;top:752px;font-size:32px}
.why-text{left:548px;top:806px;width:490px;font-size:17px;line-height:27.5px;color:#444}

/* teaser */
.teaser-title{left:175px;top:1268px;font-size:32px;color:var(--white)}
.teaser-text{left:175px;top:1328px;width:420px;font-size:13.5px;line-height:21px;color:var(--white)}
.teaser-text p+p{margin-top:12px}
.video{left:613px;top:1247px;width:434px;height:278px;background:radial-gradient(circle at 55% 50%,#1e6f6d 0%,#0d2f35 45%,#060d12 100%)}
.play{left:793px;top:1349px;width:74px;height:74px;border-radius:50%;background:#000;display:flex;align-items:center;justify-content:center}

/* team */
.team-title{left:0;width:1200px;top:1680px;text-align:center;font-size:32px}
.card{position:absolute;top:1740px;width:257px;height:378px;background:var(--white);box-shadow:0 2px 8px rgba(0,0,0,.12);text-align:center}
.card .photo{margin:15px auto 0;width:220px;height:218px;background:linear-gradient(180deg,#c9ccd0,#8a939c)}
.card h3{margin-top:22px;font-size:17px;font-weight:700}
.card .role{margin-top:6px;font-size:14px;color:var(--muted)}
.card .mail{margin-top:6px;font-size:14px;color:var(--link)}
.socials{display:flex;justify-content:center;gap:11px;margin-top:14px}
.socials span{width:32px;height:32px;border-radius:50%;background:#555}

/* product */
.product-title{left:0;width:1200px;top:2265px;text-align:center;font-size:32px;color:var(--white)}
.prod-img{top:2335px;width:388px;height:222px}
.prod-label{top:2557px;width:388px;height:56px;display:flex;align-items:center;justify-content:space-between;padding:0 24px 0 40px;font-family:"Rajdhani",sans-serif;font-weight:700;font-size:21px;text-transform:uppercase}
.prod-label svg{width:34px;height:16px}

/* testimonials */
.testi-title{left:0;width:1200px;top:2810px;text-align:center;font-size:30px}
.testi-card{left:293px;top:2880px;width:697px;height:213px;background:var(--white);box-shadow:0 2px 12px rgba(0,0,0,.15)}
.testi-photo{left:215px;top:2908px;width:155px;height:150px}
.quote{left:415px;top:2918px;width:540px;font-family:"Open Sans",sans-serif;font-style:italic;font-size:15.5px;line-height:24px;color:#666}
.author{left:417px;top:3013px;font-size:14px;font-weight:700;letter-spacing:.5px}
.tdots{left:420px;top:3055px;display:flex;gap:6px}
.tdots span{width:7px;height:7px;border-radius:50%;background:#333}
.tdots .on{background:#3a8fb0}
.qmark{left:880px;top:2990px;font-family:Georgia,serif;font-weight:700;font-size:150px;line-height:1;color:var(--ink)}

/* footer */
.foot-nav{left:135px;top:3233px;display:flex;gap:14px;font-size:18px}
.copy{left:135px;top:3268px;font-size:12px;color:#333}
.foot-social{left:910px;top:3248px;display:flex;gap:31px}
.foot-social span{width:16px;height:16px;border-radius:50%;background:#444}
</style>
</head>
<body>

<!-- section backgrounds -->
<svg class="abs" style="left:0;top:0" width="1200" height="3340" aria-hidden="true">
  <rect x="0" y="0" width="1200" height="700" fill="#1c1c1c"/>
  <polygon points="0,630 420,660 0,690" fill="#8f8f8f"/>
  <polygon points="0,690 1200,640 1200,700 0,700" fill="#ffffff"/>
  <polygon points="0,1158 1200,1140 1200,1625 0,1625" fill="#050505"/>
  <polygon points="830,1140 1200,1128 1200,1178" fill="#8f8f8f"/>
  <defs>
    <linearGradient id="teamBg" x1="0" y1="0" x2="0" y2="1">
      <stop offset="0" stop-color="#f5f5f5"/><stop offset="0.6" stop-color="#efefef"/><stop offset="1" stop-color="#cfcfcf"/>
    </linearGradient>
  </defs>
  <polygon points="0,1640 1200,1608 1200,2180 0,2228" fill="url(#teamBg)"/>
  <polygon points="0,2228 1200,2180 1200,2700 0,2740" fill="#1f1f1f"/>
  <polygon points="0,2740 1200,2700 1200,3190 0,3190" fill="#efefef"/>
</svg>

<!-- header + hero -->
<header class="hero">
  <div class="abs brand">VELMORA <i></i></div>
  <nav class="abs nav"><span>Home</span><span>About us</span><span>KYC Product</span><span>Loyalty Product</span><span>Team</span><span>Contact us</span></nav>
  <h1 class="abs display hero-title">Solving problems<br>that matter</h1>
  <p class="abs hero-sub">Create a collaborative environment for all organisation</p>
  <div class="btn btn-orange" style="left:155px;top:380px;width:182px;height:45px">Learn more
    <svg viewBox="0 0 22 12"><path d="M0 6h20M15 1l5 5-5 5" fill="none" stroke="#fff" stroke-width="1.8"/></svg></div>
  <div class="abs hero-art" role="img" aria-label="Outline illustration of stacked blockchain cubes" style="background:radial-gradient(ellipse at center,#2e2e2e 0%,#1c1c1c 70%)"></div>
  <div class="abs dots"><span class="arrow"></span><span class="on"></span><span></span><span></span><span></span><span class="arrow"></span></div>
</header>

<!-- why -->
<section>
  <div class="abs why-mark">VELMORA</div>
  <h2 class="abs display why-title">Why Velmora?</h2>
  <p class="abs why-text">Velmora Technology is a technology enabler that pledges to tackle issues that have plagued organisations for years. The company is lead by a team with tremendous expertise in the field of blockchain, mobile, IT, payment and financial sector. Being a global team, the company has influence in Singapore, China , France and more.</p>
  <div class="btn btn-dark" style="left:548px;top:1003px;width:180px;height:45px">Learn more
    <svg viewBox="0 0 22 12"><path d="M0 6h20M15 1l5 5-5 5" fill="none" stroke="#fff" stroke-width="1.8"/></svg></div>
</section>

<!-- teaser -->
<section>
  <h2 class="abs display teaser-title">Teaser video</h2>
  <div class="abs teaser-text">
    <p>Currently, Velmora is solving business problems using blockchain technology. If you have an issue that you would like to enquire, we would love to hear from you!</p>
    <p>Velmora technology leverages on the most advanced blockchain technology that might not be available a few years ago.</p>
  </div>
  <div class="btn btn-orange" style="left:175px;top:1478px;width:180px;height:44px">Watch now
    <svg viewBox="0 0 22 12"><path d="M0 6h20M15 1l5 5-5 5" fill="none" stroke="#fff" stroke-width="1.8"/></svg></div>
  <div class="abs video" role="img" aria-label="Teaser video still of glowing blockchain blocks"></div>
  <div class="abs play"><svg width="26" height="28" viewBox="0 0 26 28"><path d="M4 2l20 12-20 12z" fill="#fff"/></svg></div>
</section>

<!-- team -->
<section>
  <h2 class="abs display team-title">Our team</h2>
  <article class="card" style="left:195px">
    <div class="photo" role="img" aria-label="Portrait photo of team member"></div>
    <h3>MEMBER NAME</h3><p class="role">Founder &amp; Executive Director</p><p class="mail">info@emailaddress.com</p>
    <div class="socials"><span></span><span></span><span></span></div>
  </article>
  <article class="card" style="left:477px">
    <div class="photo" role="img" aria-label="Portrait photo of team member"></div>
    <h3>MEMBER NAME</h3><p class="role">Founder &amp; Executive Director</p><p class="mail">info@emailaddress.com</p>
    <div class="socials"><span></span><span></span><span></span></div>
  </article>
  <article class="card" style="left:760px">
    <div class="photo" role="img" aria-label="Portrait photo of team member"></div>
    <h3>MEMBER NAME</h3><p class="role">Founder &amp; Executive Director</p><p class="mail">info@emailaddress.com</p>
    <div class="socials"><span></span><span></span><span></span></div>
  </article>
</section>

<!-- product -->
<section>
  <h2 class="abs display product-title">Our product</h2>
  <div class="abs prod-img" style="left:205px;background:linear-gradient(135deg,#1d3b52,#3f6a86 50%,#12202c)" role="img" aria-label="Photo of a hand holding a glowing blockchain hologram"></div>
  <div class="abs prod-label" style="left:205px;background:var(--white);color:var(--ink)">KYC Product
    <svg viewBox="0 0 34 16"><path d="M0 8h32M25 1l7 7-7 7" fill="none" stroke="#111" stroke-width="2"/></svg></div>
  <div class="abs prod-img" style="left:610px;background:radial-gradient(circle at 50% 45%,#3a8cff,#0d3fb0 55%,#061a4d)" role="img" aria-label="Illustration of a glowing blue digital chain link"></div>
  <div class="abs prod-label" style="left:610px;background:var(--orange);color:var(--white)">Loyalty Product
    <svg viewBox="0 0 34 16"><path d="M0 8h32M25 1l7 7-7 7" fill="none" stroke="#fff" stroke-width="2"/></svg></div>
</section>

<!-- testimonials -->
<section>
  <h2 class="abs display testi-title">Testimonials</h2>
  <div class="abs testi-card"></div>
  <svg class="abs testi-photo" viewBox="0 0 155 150" role="img" aria-label="Portrait photo of the testimonial author">
    <defs><linearGradient id="face" x1="0" y1="0" x2="0" y2="1"><stop offset="0" stop-color="#d9d4cf"/><stop offset="1" stop-color="#9c7d6a"/></linearGradient></defs>
    <polygon points="40,2 115,2 153,75 115,148 40,148 2,75" fill="url(#face)"/>
  </svg>
  <p class="abs quote">Morbi diam mauris viverra in gravida eu mattis in ante Morbi eget arcu Morbi porta libero id ullamcorper nonummy nibh ligula pulvinar metus eget consectetuer augue nisi quis lacus Ut ac mi quis lacus</p>
  <p class="abs author">BY AUTHOR NAME</p>
  <div class="abs tdots"><span></span><span></span><span class="on"></span><span></span><span></span></div>
  <div class="abs qmark">”</div>
</section>

<!-- footer -->
<footer>
  <nav class="abs foot-nav"><span>Home</span><span>About us</span><span>KYC Product</span><span>Loyalty Product</span><span>Team</span><span>Contact us</span></nav>
  <p class="abs copy">© 2019 Company Name&nbsp; All right reserved</p>
  <div class="abs foot-social"><span></span><span></span><span></span></div>
</footer>

</body>
</html>
```